New Business Cards for Tormin Group

We need a new Business Card to compliment our new logo. We are a vibrant design, manufacture and install business providing recreation areas, public parks and Municipal spaces. We want business cards that are classy, modern and clean.

We have recently changed our logo, and are celebrating our 40th anniversary. We want business cards with a new modern design to reflect our status.

Target Market(s)

Customers

Contact Information for Business Card

We need all the details of our 3 offices as per the business card attached. Please disregard the old logo on the business card, the other three files show our new logo.

Requirements
Must have
• All info as per attached business card but with new logo.
Nice to have

```html
<!DOCTYPE html>
<html lang="en">
<head>
<meta charset="utf-8">
<title>Tormin Group Business Card</title>
<link href="https://fonts.googleapis.com/css2?family=Arimo:wght@400;700&display=swap" rel="stylesheet">
<style>
  :root {
    --page-bg: #e9e6e1;
    --card-white: #f7f7f7;
    --card-grey: #4a4b4e;
    --brand-red: #d8323a;
    --brand-red-dark: #c5262f;
    --text-light: #f2f2f2;
    --text-dark: #4b4c50;
  }
  * { margin: 0; padding: 0; box-sizing: border-box; }
  html, body { width: 1200px; height: 780px; overflow: hidden; }
  body {
    background: var(--page-bg);
    font-family: "Arimo", Arial, sans-serif;
    position: relative;
  }
  .card {
    position: absolute;
    top: 225px;
    width: 560px;
    height: 330px;
    overflow: hidden;
    box-shadow: 0 6px 18px rgba(0,0,0,0.18);
  }
  .card-front { left: 40px; background: var(--card-grey); }
  .card-back {
    left: 620px;
    background: linear-gradient(160deg, var(--brand-red) 0%, var(--brand-red-dark) 100%);
  }
  .front-shapes { position: absolute; inset: 0; }
  .logo {
    position: absolute;
    display: flex;
    align-items: center;
    gap: 10px;
  }
  .logo-mark { border-radius: 50%; flex: none; }
  .logo-name { font-weight: 700; letter-spacing: 0.5px; white-space: nowrap; }
  .card-front .logo { left: 190px; top: 16px; }
  .card-front .logo-mark { width: 32px; height: 32px; background: var(--brand-red); }
  .card-front .logo-name { font-size: 25px; color: var(--text-dark); }

  .contact-person {
    position: absolute;
    left: 330px;
    top: 132px;
    color: var(--text-light);
    width: 210px;
  }
  .person-name { font-size: 15px; font-weight: 700; }
  .person-role { font-size: 11px; margin-top: 2px; }
  .person-details { font-size: 10.5px; line-height: 14px; margin-top: 12px; }

  .offices {
    position: absolute;
    left: 28px;
    top: 124px;
    color: var(--text-light);
  }
  .office + .office { margin-top: 6px; }
  .office-title { font-size: 12px; line-height: 14px; font-weight: 700; margin-bottom: 1px; }
  .office-line { font-size: 9.5px; line-height: 11.5px; }

  .world-map {
    position: absolute;
    left: 70px; top: 30px;
    width: 440px; height: 270px;
    border-radius: 40% 50% 45% 40%;
    background: radial-gradient(ellipse at center, rgba(240,120,125,0.55) 0%, rgba(240,120,125,0.25) 60%, rgba(240,120,125,0) 80%);
  }
  .card-back .logo {
    left: 50%; top: 50%;
    transform: translate(-50%, -50%);
  }
  .card-back .logo-mark { width: 48px; height: 48px; background: var(--text-light); }
  .card-back .logo-name { font-size: 38px; color: var(--text-light); }
  .website {
    position: absolute;
    left: 60px;
    top: 62px;
    color: var(--text-light);
    font-size: 11px;
    letter-spacing: 2px;
  }
</style>
</head>
<body>

<section class="card card-front" aria-label="Business card front">
  <svg class="front-shapes" width="560" height="330" viewBox="0 0 560 330" aria-hidden="true">
    <path d="M0 0 H560 V26 C430 80 230 102 0 88 Z" fill="var(--card-white)"/>
    <path d="M0 88 C230 102 430 80 560 26 L560 32 C430 88 230 112 0 98 Z" fill="var(--brand-red)"/>
    <path d="M0 98 C230 112 430 88 560 32 L560 36 C430 93 230 117 0 103 Z" fill="var(--card-white)" opacity="0.9"/>
  </svg>

  <div class="logo">
    <span class="logo-mark"></span>
    <span class="logo-name">TORMIN GROUP</span>
  </div>

  <div class="contact-person">
    <p class="person-name">Marek Solvane</p>
    <p class="person-role">Managing Partner</p>
    <p class="person-details">Mobile No: +971 (0)50 555 0351<br>Email: marek@tormingroup.com</p>
  </div>

  <div class="offices">
    <div class="office">
      <p class="office-title">Head Office</p>
      <p class="office-line">P.O. Box: 40112 Abu Dhabi, U.A.E.</p>
      <p class="office-line">Tel No: +971 (0)2 5550184</p>
      <p class="office-line">Fax No: +971 (0)2 5550183</p>
      <p class="office-line">Email: sales@tormingroup.com</p>
    </div>
    <div class="office">
      <p class="office-title">Dubai Office</p>
      <p class="office-line">P.O. Box: 58210 Dubai, U.A.E.</p>
      <p class="office-line">Tel No: +971 (0)4 5550691</p>
      <p class="office-line">Fax No: +971 (0)4 5550769</p>
      <p class="office-line">Email: sales@tormingroup.com</p>
    </div>
    <div class="office">
      <p class="office-title">Qatar Office</p>
      <p class="office-line">P.O. Box: 27734 Doha, Qatar</p>
      <p class="office-line">Tel No: +974 55510195</p>
      <p class="office-line">Fax No: +974 55510260</p>
      <p class="office-line">Email: sales@tormingroup.com</p>
    </div>
  </div>
</section>

<section class="card card-back" aria-label="Business card back">
  <div class="world-map" role="img" aria-label="Faint world map spread across the card"></div>
  <div class="logo">
    <span class="logo-mark"></span>
    <span class="logo-name">TORMIN GROUP</span>
  </div>
  <p class="website">www.tormingroup.com</p>
</section>

</body>
</html>
```